Health & Fitness Retreat Homepage Design

We have an existing website at http://www.BrightMeadowStays.com.au which we are retaining but wish to have a freshly designed homepage with the existing top navigation bar.
Sample layout is attached, but feel free to use your creativity on layout and colours, always remembering it needs to fit with the wider site design.
Project Delivery:
5 phase slide slow at top of homepage
Full homepage design and associated files
Target Audience:
- Female 80%, Male 20%
- Aged 30 to 50
- Overweight/Obese (so no pictures of thin people)
See attached layout for more information.
Target Market(s)
Target Audience:
- Female 80%, Male 20%
- Aged 30 to 50
Industry/Entity Type
Fitness
Requirements
Must have
- Must have existing top navigation bar as at http://www.BrightMeadowStays.com.au and fit with existing interior colours, etc.
Should not have
- No pictures of thin people

```html
<!DOCTYPE html>
<html lang="en">
<head>
<meta charset="utf-8">
<title>Bright Meadow Weight Loss Retreat</title>
<link rel="stylesheet" href="https://fonts.googleapis.com/css2?family=Open+Sans:ital,wght@0,400;0,600;0,700;1,400;1,700&display=swap">
<style>
:root{
  --page:#dcd6cc;
  --paper:#ffffff;
  --cream:#f3f0eb;
  --orange:#f39220;
  --orange-dark:#e07d10;
  --orange-text:#e8861a;
  --green:#8cc63f;
  --green-dark:#4a9a12;
  --green-light:#a9d65e;
  --text:#777067;
  --text-light:#9a948b;
  --taupe:#b8ae9f;
  --peach:#fdf1e0;
}
*{margin:0;padding:0;box-sizing:border-box}
html,body{width:900px;height:1200px;overflow:hidden}
body{position:relative;background:linear-gradient(var(--page) 0 1020px,#e3ded6 1020px);font-family:"Open Sans",Arial,sans-serif;color:var(--text)}
.abs{position:absolute}
.sheet{left:45px;top:15px;width:810px;height:1140px;background:var(--paper);box-shadow:0 0 6px rgba(0,0,0,.08)}
.header-curve{left:505px;top:15px;width:350px;height:98px}
.brand{left:87px;top:52px;display:flex;align-items:center;gap:8px}
.brand-dot{width:30px;height:30px;border-radius:50%;background:var(--orange)}
.brand-name{font-weight:700;font-size:15px;color:var(--green-dark);line-height:1.1}
.brand-name small{display:block;font-size:9px;color:#555}
.btn-brochure{left:540px;top:55px;width:145px;height:38px;border-radius:6px;background:linear-gradient(#7dc93b,#3f8d0d);color:#fff;font-style:italic;font-size:15px;display:flex;align-items:center;justify-content:center;transform:skewX(-8deg);white-space:nowrap}
.btn-magazine{left:693px;top:48px;width:140px;height:44px;border-radius:22px;background:linear-gradient(#ffa33c,#ee6a06);color:#fff;font-size:14px;display:flex;align-items:center;padding-left:64px}
.mag-tag{left:720px;top:44px;width:30px;height:52px;background:#eee8df;color:var(--orange-dark);font-size:10px;font-weight:700;writing-mode:vertical-rl;transform:rotate(180deg);display:flex;align-items:center;justify-content:center}
.nav-band{left:45px;top:113px;width:600px;height:125px;background:linear-gradient(var(--orange),var(--orange-dark))}
.nav-col{top:126px}
.nav-col h3{color:#fff;font-size:11px;font-weight:700;margin:0 0 8px 3px;white-space:nowrap}
.nav-box{background:#f4f1ec;border-radius:5px;padding:8px 12px;font-size:9px;line-height:20.5px;height:80px;color:var(--text);white-space:nowrap}
.side-menu{left:647px;top:113px;width:208px;height:125px;background:linear-gradient(var(--green-light),var(--green));border:1px solid #c8e59c}
.side-menu a{display:block;color:#fff;font-size:13.5px;padding:0 0 0 17px;height:27.5px;line-height:27.5px;border-bottom:1px solid rgba(255,255,255,.55);text-decoration:none;white-space:nowrap;overflow:hidden;letter-spacing:-.1px}
.slider{left:62px;top:259px;width:780px;height:233px;background:#fff;border:1px solid #cfcac2;box-shadow:0 8px 12px -6px rgba(0,0,0,.25)}
.slide-photo{left:69px;top:268px;width:236px;height:215px;background:linear-gradient(90deg,#f2f2f2,#fafafa)}
.slide-title{left:310px;top:288px;width:420px;text-align:center;font-size:24px;font-weight:700;font-style:italic;color:#f4a54a}
.slide-text{left:300px;top:336px;width:495px;text-align:center;font-size:9px;font-style:italic;line-height:17px;color:var(--text-light)}
.btn-more{left:425px;top:391px;width:190px;height:41px;border-radius:5px;background:linear-gradient(#7ccb38,#2f8305);color:#fff;font-size:14px;display:flex;align-items:center;justify-content:center;box-shadow:0 8px 10px -6px rgba(0,0,0,.3)}
.dots{left:752px;top:468px;display:flex;gap:3px}
.dots i{width:7px;height:7px;border-radius:50%;background:var(--orange)}
.dots i:last-child{background:var(--green)}
.welcome-title{left:69px;top:514px;font-size:14px;color:#6aa51f}
.welcome-text{left:77px;top:540px;width:560px;font-size:9.6px;line-height:17.2px}
.welcome-text p+p{margin-top:17px}
.results{left:647px;top:507px;width:188px;height:383px;background:linear-gradient(#f4f0ea,#fff);border-radius:6px;padding:15px 12px}
.results h4{font-size:9.5px;line-height:17px;font-weight:600;color:var(--orange-dark)}
.results h4 span{color:var(--green-dark)}
.results ul{list-style:none;margin-top:23px;font-size:9.5px;line-height:17.1px}
.results li{padding-left:9px;position:relative}
.results li::before{content:"";position:absolute;left:0;top:7px;width:4px;height:4px;border-radius:50%;background:#f4b56c}
.card{top:745px;width:253px;height:216px;border:1px solid #ddd}
.card h3{font-size:15px;font-weight:400;color:var(--orange-dark);margin:14px 0 0 13px}
.video{left:69px;background:#f1eee9}
.video-frame{left:85px;top:785px;width:222px;height:130px;background:linear-gradient(#7a3b2a,#c77a4e)}
.video-bar{left:85px;top:915px;width:222px;height:14px;background:linear-gradient(#eee,#bbb);border:1px solid #999}
.video-bar i{position:absolute;left:20px;top:5px;width:70px;height:3px;background:#d33}
.play{left:172px;top:848px;width:34px;height:34px;border-radius:50%;background:rgba(0,0,0,.45)}
.play::after{content:"";position:absolute;left:13px;top:10px;border-left:11px solid #fff;border-top:7px solid transparent;border-bottom:7px solid transparent}
.testimonials{left:344px;background:var(--peach);border-color:#f7dcb6}
.quote{left:355px;width:235px;display:flex;gap:7px}
.quote-photo{width:70px;height:59px;background:linear-gradient(#e9d6cc,#c99585);border:2px solid #fff;flex:none}
.quote p{font-size:10px;line-height:16px;color:var(--orange-dark)}
.quote time{display:block;font-size:10px;font-style:italic;color:#999;margin:6px 0 0 20px}
.quote-rule{left:355px;top:859px;width:225px;border-top:2px dashed #e2a765}
.footer{left:45px;top:973px;width:810px;height:142px;background:#f3f1ee}
.foot-col{top:995px;font-size:9.5px;white-space:nowrap}
.foot-col h5{font-size:9.5px;font-weight:400;color:var(--text-light);margin-bottom:18px}
.foot-col li{list-style:none;line-height:15.5px;padding-left:9px;position:relative}
.foot-col li::before{content:"";position:absolute;left:0;top:6px;width:4px;height:4px;border-radius:50%;background:#f4b56c}
.contact-title{left:513px;top:989px;font-size:13px;color:var(--orange-dark)}
.contact-form{left:510px;top:1010px;width:308px;height:105px;background:linear-gradient(#f59a2a,var(--orange-dark));border-radius:4px 4px 0 0}
.label{font-size:9.5px;color:#fff}
.field{background:#f8f5f0;border-radius:3px}
.submit{left:711px;top:1080px;width:82px;height:27px;border-radius:4px;background:linear-gradient(#555,#111);color:#fff;font-size:10px;display:flex;align-items:center;justify-content:center}
.bottom-bar{left:45px;top:1115px;width:810px;height:40px;background:var(--taupe);color:#fff;font-size:10px;display:flex;align-items:center;padding-left:27px;white-space:nowrap}
.bottom-bar span{white-space:pre}
.rights{margin-left:auto;margin-right:33px}
.social{top:1167px;width:27px;height:27px;border-radius:50%;background:#fff;border:3px solid #e8e6e2}
</style>
</head>
<body>
<div class="abs sheet"></div>
<svg class="abs header-curve" viewBox="0 0 350 98" aria-hidden="true"><path d="M10 98 C20 30 80 5 180 0 H350 V98 Z" fill="#efebe5"/></svg>

<div class="abs brand"><span class="brand-dot"></span><div class="brand-name">BRIGHT MEADOW<small>WEIGHT LOSS RETREAT</small></div></div>
<div class="abs btn-brochure">FREE BROCHRE!!!</div>
<div class="abs btn-magazine">MAGAZINE</div>
<div class="abs mag-tag">FREE</div>

<nav class="abs nav-band"></nav>
<div class="abs nav-col" style="left:70px;width:130px"><h3>The Best Programs</h3><div class="nav-box">Weight Loss Retreat<br>Fitness Camps<br>Home Retreat</div></div>
<div class="abs nav-col" style="left:225px;width:130px"><h3>The Best Locations</h3><div class="nav-box">Blue Mountains, NSW<br>Central Coast, NSW<br>Victoria (Torquay)</div></div>
<div class="abs nav-col" style="left:372px;width:232px"><h3>About Bright Meadow</h3><div class="nav-box" style="display:flex;gap:10px;padding:8px 10px"><div>Why choose Bright Meadow<br>What clients say....<br>Contact us</div><div style="border-left:1px solid #ccc;padding-left:9px">FREE Brochure<br>Special Offers</div></div></div>
<div class="abs side-menu"><a>Weight Loss Retreats</a><a>Fitness Camps &amp; Holidays</a><a>Home Program</a><a style="border:0">Special Offers</a></div>

<div class="abs slider"></div>
<div class="abs slide-photo" role="img" aria-label="Woman holding a burger and a syringe"></div>
<div class="abs slide-title">Real People, Proven Results</div>
<div class="abs slide-text">Whether you are looking for a fat camp, weight loss camp, fitness retreat or luxury health retreat to give you a quick kick start with your weight loss or want a program that will help you change your health</div>
<div class="abs btn-more">MORE INFORMATION</div>
<div class="abs dots"><i></i><i></i><i></i><i></i></div>

<h2 class="abs welcome-title" style="font-weight:400">Welcome To BRIGHT MEADOW</h2>
<div class="abs welcome-text">
<p>You will lose weight, drop fat, reduce centimetres and transform your body and your life at Australia's No. 1 Weight Loss Retreat, Fitness Retreat &amp; Lifestyle Change Health Retreats in NSW close to Sydney and Victoria Weight Loss Health Retreats close to Melbourne. You will feel comfortable and among like minded people at our Weight Loss &amp; Fitness Health Retreats program which is suitable for adults of all ages, shapes, sizes and fitness levels.</p>
<p>Whether you are looking for a fat camp, weight loss camp, fitness retreat or luxury health retreat to give you a quick kick start with your weight loss or want a program that will help you change your health and your habits for the long term your time at Bright Meadow Weight Loss Health Retreats will be life changing. With weight loss retreats in NSW close to Sydney as well as luxury weight loss health retreats in Victoria close to Melbourne you will be able to choose from a range of stunning surroundings. Our Weight Loss Retreats in NSW include the Blue Mountains and NSW Central Coast as well as our Victoria Weight Loss Retreat in Torquay close to Melbourne.</p>
</div>

<aside class="abs results">
<h4>AMAZING RESULTS<br><span>FOR PEOPLE OF ALL AGES, SHAPES, SIZES AND FITNESS LEVEL.</span></h4>
<ul><li>Weight loss</li><li>Fat loss</li><li>Lose centimetres of your waist, hips, thighs and from all over your body Increased flexibility</li><li>Improved mobility and agility</li><li>Transform your skin condition</li><li>Feel happier</li><li>Eliminate high blood pressure</li><li>Eliminate Type 2 Diabetes</li><li>Reduce cholesterol issues</li><li>Improve previous injuries</li><li>Reduce head aches</li><li>Reduce stress</li><li>No more anxiety</li><li>Significant improvements for those suffering depression</li></ul>
</aside>

<section class="abs card video"><h3>Our Video</h3></section>
<div class="abs video-frame" role="img" aria-label="Video still of a smiling client"></div>
<div class="abs play"></div>
<div class="abs video-bar"><i></i></div>

<section class="abs card testimonials"><h3>Testimonials</h3></section>
<div class="abs quote" style="top:789px"><div class="quote-photo" role="img" aria-label="Client portrait"></div><div><p>"The best weight loss experience of my life"</p><time>Feb 24, 2012</time></div></div>
<div class="abs quote-rule"></div>
<div class="abs quote" style="top:876px"><div class="quote-photo" role="img" aria-label="Client portrait"></div><div><p>"The best weight loss experience of my life"</p><time>Feb 24, 2012</time></div></div>

<footer class="abs footer"></footer>
<div class="abs foot-col" style="left:90px"><h5>The Best Programs</h5><ul><li>Weight Loss Retreat</li><li>Fitness Boot Camp</li><li>Home program</li></ul></div>
<div class="abs foot-col" style="left:220px"><h5>The Best Locations</h5><ul><li>Blue Mountains, NSW</li><li>Central Coast, NSW</li><li>Victoria (Torquay)</li></ul></div>
<div class="abs foot-col" style="left:349px"><h5>About Us</h5><ul><li>Contact us</li><li>Why choose Bright Meadow</li><li>What clients say....</li><li>Book now</li></ul></div>

<h3 class="abs contact-title" style="font-weight:400">Contact Form</h3>
<div class="abs contact-form"></div>
<span class="abs label" style="left:528px;top:1025px">Name</span>
<span class="abs field" style="left:568px;top:1024px;width:90px;height:17px"></span>
<span class="abs label" style="left:675px;top:1025px">Email</span>
<span class="abs field" style="left:715px;top:1024px;width:90px;height:17px"></span>
<span class="abs label" style="left:528px;top:1052px">Message</span>
<span class="abs field" style="left:570px;top:1050px;width:91px;height:58px"></span>
<span class="abs label" style="left:675px;top:1053px">Phone</span>
<span class="abs field" style="left:714px;top:1051px;width:90px;height:17px"></span>
<div class="abs submit">SUBMIT</div>

<div class="abs bottom-bar"><span>Home         |   The Best Programs   |   The Best Locations About Bright Meadow   |   Contact Us</span><span class="rights">All Rights Reserved. http://www.BrightMeadowStays.com.au/</span></div>

<span class="abs social" style="left:690px"></span>
<span class="abs social" style="left:722px"></span>
<span class="abs social" style="left:755px"></span>
<span class="abs social" style="left:788px"></span>
<span class="abs social" style="left:821px"></span>
</body>
</html>
```